Web Design for Harbor Link Guild

We need a web design for Harbor Link Guild. You can see more details about the kind of business that it deals with in this link: http://harborlinkguild.example/. The concept of the site is similar to http://www.volmari.example/ and we are looking for a homepage design also similar to it.
The top navigation should have:
1) directory
2) articles
3) deals
4) forums
5) log in/register page.
It should also have a video, a slider, map & text as well as a call to action to a "why register page".
As part of the footer it should include:
1) about HLG
2) contact HGL
3) terms & conditions
4) privacy
The color palette for the site will be the UAE flag colors which are red, green, white and black.
Updates
Project Deadline Extended
Reason: We need more designs and options.
Keep sending in more creative designs. thanks.
Industry/Entity Type
Business
Look and feel
Each slider illustrates characteristics of the customer's brand and the style your logo design should communicate.

```html
<!DOCTYPE html>
<html lang="en">
<head>
<meta charset="utf-8">
<title>Harbor Link Guild</title>
<link href="https://fonts.googleapis.com/css2?family=Open+Sans:wght@400;600&family=Arimo&display=swap" rel="stylesheet">
<style>
:root{
  --red:#d0121b;
  --green:#138a4a;
  --green-dark:#0d6b38;
  --ink:#2b2b2b;
  --text:#444;
  --muted:#666;
  --nav:#2e2e2e;
  --btn:#3a3a3a;
  --rule:#cfcfcf;
  --gold:#c9940f;
  --black:#000;
}
*{margin:0;padding:0;box-sizing:border-box}
html,body{width:1200px;height:1050px;overflow:hidden;background:#fff}
body{position:relative;font-family:"Open Sans",sans-serif;color:var(--text)}
.abs{position:absolute}

.brand{left:120px;top:34px;display:flex;align-items:center;gap:12px}
.brand-mark{width:30px;height:30px;background:var(--red)}
.brand-name{font-size:26px;font-weight:600;color:var(--green);line-height:1}

.contact{right:124px;top:33px;font-size:12px;color:var(--ink)}
.cta{left:910px;top:69px;width:170px;height:33px;background:linear-gradient(#1a9b55,var(--green-dark));border:1px solid #0b5e31;border-radius:2px;color:#fff;font-size:14px;font-weight:600;display:flex;align-items:center;gap:14px;padding-left:16px}

.nav{left:120px;top:122px;width:960px;height:38px;background:linear-gradient(#3a3a3a,#232323)}
.nav a{position:absolute;top:0;height:38px;line-height:38px;color:#fff;font-size:14px;font-weight:600;text-decoration:none}
.nav .active{left:0;width:106px;background:var(--red);text-align:center}
.search{position:absolute;left:716px;top:4px;width:240px;height:30px;background:#fff;border:1px solid #999}
.search svg{position:absolute;right:10px;top:8px}

.slider{left:120px;top:168px;width:960px;height:340px;background:linear-gradient(90deg,#e9ecee 0%,#f7f7f7 35%,#eef0f1 60%,#d6d8da 85%,#4a4c52 100%)}
.dots{left:552px;top:482px;display:flex;gap:7px}
.dots span{width:14px;height:14px;border-radius:50%;background:#555;opacity:.8}
.dots span:first-child{background:#ddd}

.col{top:531px;width:300px}
.col h2{font-size:15px;font-weight:600;color:var(--ink);letter-spacing:.2px}
.photo{position:absolute;left:0;width:300px;box-shadow:0 1px 3px rgba(0,0,0,.35)}
.welcome .photo{top:47px;height:140px;background:linear-gradient(90deg,#b79a86,#e8e2dc 40%,#cfc8c4 70%,#6b5a55)}
.welcome p{position:absolute;top:192px;font-size:12px;line-height:18px;text-align:justify;color:var(--text)}
.mission ul{list-style:none;position:absolute;top:45px;width:300px}
.mission li{position:relative;padding-left:27px;font-size:11.5px;line-height:14.5px;text-align:justify;margin-bottom:14px;color:var(--text)}
.mission li::before{content:"";position:absolute;left:0;top:1px;width:13px;height:13px;background:var(--green)}
.mission li::after{content:"";position:absolute;left:5px;top:4px;border-left:5px solid #fff;border-top:3.5px solid transparent;border-bottom:3.5px solid transparent}
.works .photo{top:47px;height:212px;background:linear-gradient(120deg,#8a7b70,#d9d2c9 45%,#bfcfd3 60%,#5a4a42)}
.play{position:absolute;left:98px;top:80px;width:108px;height:66px;border-radius:6px;background:rgba(255,255,255,.35);border:1px solid rgba(255,255,255,.6)}
.play::after{content:"";position:absolute;left:42px;top:14px;border-left:30px solid rgba(255,255,255,.85);border-top:19px solid transparent;border-bottom:19px solid transparent}
.btn{position:absolute;top:290px;height:31px;padding:0 7px;line-height:31px;background:var(--btn);color:#fff;font-size:12.5px;font-weight:600;box-shadow:1px 1px 2px rgba(0,0,0,.4)}

.rule{left:120px;top:890px;width:960px;height:1px;background:var(--rule)}
.foot-brand{left:122px;top:930px;display:flex;align-items:center;gap:8px}
.foot-brand .brand-mark{width:18px;height:18px}
.foot-brand .brand-name{font-size:15px}
.vline{width:1px;top:908px;height:66px}
.patron-badge{left:341px;top:912px;width:44px;height:58px;border-radius:8px 8px 22px 22px;background:linear-gradient(var(--gold),#8e6a0c)}
.patron{left:395px;top:918px;width:260px;text-align:center;font-weight:600;line-height:16px}
.patron .a,.patron .p{color:var(--black);font-size:13px}
.patron .name{color:var(--gold);font-size:13.5px;text-align:left}
.follow{left:740px;top:929px;font-size:18px;color:var(--muted)}
.social{left:860px;top:923px;display:flex;gap:8px}
.social span{width:30px;height:30px}

.bottom{left:0;top:992px;width:1200px;height:58px;background:var(--black)}
.bottom p{position:absolute;left:0;width:1200px;top:18px;text-align:center;font-family:"Arimo",sans-serif;font-size:12px;color:#8a8a8a}
</style>
</head>
<body>

<header>
  <div class="abs brand"><span class="brand-mark"></span><span class="brand-name">Harbor Link Guild</span></div>
  <div class="abs contact">T: +971 (4) 555 0173 | F: +971 (4) 555 0186</div>
  <a class="abs cta">
    <svg width="22" height="22" viewBox="0 0 22 22"><rect x="1" y="3" width="16" height="17" fill="none" stroke="#fff" stroke-width="2"/><path d="M8 14 L19 3 L21 5 L10 16 L7 17 Z" fill="#fff"/></svg>
    WHY REGISTER?
  </a>
</header>

<nav class="abs nav">
  <a class="active">HOME</a>
  <a style="left:136px">DIRECTORY</a>
  <a style="left:274px">ARTICLES</a>
  <a style="left:402px">DEALS</a>
  <a style="left:510px">FORUMS</a>
  <a style="left:634px">LOG IN</a>
  <div class="search"><svg width="14" height="12" viewBox="0 0 14 12"><circle cx="4.5" cy="4.5" r="3" fill="none" stroke="#222" stroke-width="2"/><path d="M7 7 L12 11" stroke="#222" stroke-width="2.5"/></svg></div>
</nav>

<div class="abs slider" role="img" aria-label="Slider photo: business people in conversation in a bright office"></div>
<div class="abs dots"><span></span><span></span><span></span><span></span><span></span></div>

<section class="abs col welcome" style="left:120px">
  <h2>WELCOME TO HARBOR LINK GUILD</h2>
  <div class="photo" role="img" aria-label="Photo of a smiling businessman in front of his team"></div>
  <p>Lorem ipsum dolor sit amet, consectetur adipisicing elit, sed do eiusmod tempor incididunt ut labore et dolore magna aliqua. Ut enim ad minim veniam, quis nostrud exercitation ullamco laboris nisi ut al</p>
  <span class="btn">Read More</span>
</section>

<section class="abs col mission" style="left:450px">
  <h2>OUR MISSION</h2>
  <ul>
    <li>Harbor Link Guild will allow you to maximize the potential of your Free Zone business.</li>
    <li>A business Networking Platform helping Free Zone members' source new customers.</li>
    <li>Provide a supportive infrastructure to enable companies to access and engage in unlimited networking opportunities.</li>
    <li>Build mutual business relationships with fellow Free Zone companies.</li>
    <li>As a Harbor Link Guild member, you will have the opportunity to improve business techniques...</li>
  </ul>
  <span class="btn">Read More</span>
</section>

<section class="abs col works" style="left:780px">
  <h2>HOW IT WORKS</h2>
  <div class="photo" role="img" aria-label="Video still: a group of colleagues looking at a screen together"><span class="play"></span></div>
  <span class="btn">See More</span>
</section>

<footer>
  <div class="abs rule"></div>
  <div class="abs foot-brand"><span class="brand-mark"></span><span class="brand-name">Harbor Link Guild</span></div>
  <div class="abs vline" style="left:319px;background:#7fb893"></div>
  <div class="abs patron-badge"></div>
  <div class="abs patron"><div class="a">A</div><div class="name">Sheikh Rashid bin Omar Al Nouri</div><div class="p">Project</div></div>
  <div class="abs vline" style="left:693px;background:var(--rule)"></div>
  <div class="abs follow">Follow us</div>
  <div class="abs social">
    <span style="background:#3b5a9a"></span>
    <span style="background:#2aa7e0"></span>
    <span style="background:#2b2b2b"></span>
    <span style="background:#e0262c"></span>
    <span style="background:#d8201c"></span>
    <span style="background:#f39a1d"></span>
  </div>
  <div class="abs bottom"><p>© 2013 Harbor Link Guild | All Rights Reserved</p></div>
</footer>

</body>
</html>
```